Brindle Healthcare Coming Soon Sign

I need a large (10 x5) road banner announcing the construction of our new medical practice at 5187 Larkmoor Road in John's Island. The name of our practice is Brindle Healthcare and we thought it would be fund to nick name it the "Brindle Waystation". We'd like the tagline to read - "There's nothing healthy about driving an hour to see your doctor. So we're coming to you." Opening Late 2025 I have attached three logos as we have two other practices (Brindle Urgent and Brindle Aesthetics ) that should be present on the bottom of the sign but the main business is Brindle Healthcare. For more information on our look/feel visit our website www.goplainway-example.com (which should be somewhere on the banner as well)
Updates

The signage needs to say Coming Late Fall 2025!

Target Market(s)

Drive By traffic must be made aware that we are coming soon

Industry/Entity Type

Healthcare

Requirements
Nice to have
• Western Theme

```html
<!DOCTYPE html>
<html lang="en">
<head>
<meta charset="utf-8">
<title>Brindle Healthcare – Coming Late Fall 2025</title>
<link rel="stylesheet" href="https://fonts.googleapis.com/css2?family=Alfa+Slab+One&family=Inter:wght@600;700&family=Montserrat:wght@700&display=swap">
<style>
  :root {
    --backdrop: #8a8a8a;
    --paper: #ffffff;
    --navy: #243663;
    --sky: #6bb5e4;
    --red: #e83a40;
    --pink: #e81c79;
    --charcoal: #2f3a33;
    --grain: #f3f3e8;
    --rule: #e4e6da;
  }
  * { margin: 0; padding: 0; box-sizing: border-box; }
  html, body { width: 1200px; height: 2173px; overflow: hidden; background: var(--backdrop); }
  .canvas { position: relative; width: 1200px; height: 2173px; }
  .artwork { position: absolute; inset: 0; width: 1200px; height: 2173px; }
  .text-block { position: absolute; left: 0; width: 1200px; text-align: center; }

  .brand-name {
    font-family: "Montserrat", sans-serif;
    font-weight: 700;
    color: var(--navy);
    line-height: 1;
  }
  .brand-name .word-primary { display: block; font-size: 80px; letter-spacing: 18px; margin-right: -18px; }
  .brand-name .word-secondary { display: block; font-size: 49px; letter-spacing: 13px; margin-right: -13px; margin-top: 22px; }

  .announcement {
    top: 838px;
    font-family: "Alfa Slab One", serif;
    font-size: 78px;
    line-height: 74px;
    color: var(--navy);
    text-transform: uppercase;
  }
  .announcement .highlight { color: var(--red); }

  .tagline {
    top: 1203px;
    font-family: "Inter", sans-serif;
    font-weight: 600;
    font-size: 43px;
    line-height: 55px;
    color: var(--navy);
  }

  .sister-brand {
    position: absolute;
    top: 1588px;
    width: 360px;
    text-align: center;
    font-family: "Montserrat", sans-serif;
    font-weight: 700;
    color: var(--charcoal);
    line-height: 1;
  }
  .sister-brand .word-primary { display: block; font-size: 42px; letter-spacing: 9px; margin-right: -9px; }
  .sister-brand .word-secondary { display: block; font-size: 30px; letter-spacing: 10px; margin-right: -10px; margin-top: 14px; }
  .sister-urgent { left: 223px; }
  .sister-aesthetics { left: 619px; }

  .website {
    top: 1778px;
    font-family: "Inter", sans-serif;
    font-weight: 700;
    font-size: 38px;
    color: var(--navy);
  }
</style>
</head>
<body>
<main class="canvas">
  <svg class="artwork" viewBox="0 0 1422 2576" aria-hidden="false">
    <rect class="sign-panel" x="154" y="173" width="1115" height="2230" fill="var(--paper)"/>
    <path class="sign-frame" fill="none" stroke="var(--navy)" stroke-width="30"
      d="M482 272 Q711 70 940 272 L1062 272 L1062 380 Q1255 400 1255 590 L1255 1990
         Q1255 2180 1062 2197 L1062 2305 L940 2305 Q711 2500 482 2305 L360 2305 L360 2197
         Q168 2180 168 1990 L168 590 Q168 400 360 380 L360 272 Z"/>
    <circle class="brand-marker" cx="711" cy="490" r="72" fill="var(--sky)"/>
    <rect class="wood-band" x="185" y="917" width="1052" height="405" fill="var(--grain)"
      role="img" aria-label="Faint pale wood-grain texture behind the opening announcement"/>
    <line class="divider-rule" x1="293" y1="1723" x2="1130" y2="1723" stroke="var(--rule)" stroke-width="2"/>
    <line class="divider-rule" x1="293" y1="2034" x2="1130" y2="2034" stroke="var(--rule)" stroke-width="2"/>
    <line class="divider-column" x1="711" y1="1767" x2="711" y2="1985" stroke="var(--rule)" stroke-width="2"/>
    <circle class="urgent-marker" cx="478" cy="1818" r="36" fill="var(--red)"/>
    <circle class="aesthetics-marker" cx="947" cy="1818" r="36" fill="var(--pink)"/>
    <g class="star-row" fill="var(--navy)">
      <polygon points="638,2256 643,2270 658,2270 646,2279 650,2293 638,2284 626,2293 630,2279 618,2270 633,2270"/>
      <polygon points="711,2268 716,2282 731,2282 719,2291 723,2305 711,2296 699,2305 703,2291 691,2282 706,2282"/>
      <polygon points="784,2256 789,2270 804,2270 792,2279 796,2293 784,2284 772,2293 776,2279 764,2270 779,2270"/>
    </g>
  </svg>

  <h1 class="text-block brand-name" style="top:536px;">
    <span class="word-primary">BRINDLE</span>
    <span class="word-secondary">HEALTHCARE</span>
  </h1>

  <p class="text-block announcement">
    <span class="highlight">Coming</span><br>Late<br>Fall 2025!
  </p>

  <p class="text-block tagline">
    Conserving Rural John's Island<br>with Home Grown Progressive<br>Primary Care
  </p>

  <div class="sister-brand sister-urgent">
    <span class="word-primary">BRINDLE</span>
    <span class="word-secondary">URGENT</span>
  </div>
  <div class="sister-brand sister-aesthetics">
    <span class="word-primary">BRINDLE</span>
    <span class="word-secondary">AESTHETICS</span>
  </div>

  <p class="text-block website">www.goplainway-example.com</p>
</main>
</body>
</html>
```